TA BRAMLEY BUSINESS CARD DESIGN PROJECT

We need to utilize our logo that was expertly created on PixelHarbor and now need to match this with a business card design.

```html
<!DOCTYPE html>
<html lang="en">
<head>
<meta charset="UTF-8">
<title>TA BRAMLEY Business Card</title>
<link href="https://fonts.googleapis.com/css2?family=Montserrat:wght@400;500;700&display=swap" rel="stylesheet">
<style>
  :root {
    --page-bg: #e9e6e2;
    --card-bg: #161616;
    --card-back-bg: #1a1a1a;
    --brand-blue: #1559b8;
    --text-light: #f2f2f2;
    --emboss: #2b2b2b;
    --line-dark: #0c0c0c;
  }
  * { margin: 0; padding: 0; box-sizing: border-box; }
  html, body {
    width: 1200px; height: 834px; overflow: hidden;
    background: var(--page-bg);
    font-family: "Montserrat", sans-serif;
  }
  .canvas {
    position: relative; width: 1200px; height: 834px;
    display: flex; align-items: center; justify-content: center; gap: 40px;
  }
  .card {
    position: relative; width: 540px; height: 309px;
    border-radius: 24px; overflow: hidden;
    box-shadow: 0 10px 24px rgba(0,0,0,0.25);
  }
  .card-front { background: var(--card-bg); }
  .card-back {
    background: var(--card-back-bg);
    display: flex; align-items: center; justify-content: center;
  }
  .wave-band { position: absolute; left: 0; bottom: 0; width: 540px; height: 309px; }
  .brand-name {
    position: absolute; left: 34px; top: 92px; width: 200px;
    color: var(--brand-blue); font-weight: 700;
    font-size: 30px; letter-spacing: 4px; line-height: 1.15; text-align: center;
  }
  .brand-mark {
    display: block; width: 14px; height: 14px; margin: 0 auto 10px;
    background: var(--brand-blue); border-radius: 50%;
  }
  .divider {
    position: absolute; left: 252px; top: 52px;
    width: 1px; height: 178px; background: var(--brand-blue);
  }
  .contact { position: absolute; left: 272px; top: 50px; color: var(--text-light); }
  .contact-name {
    color: var(--brand-blue); font-weight: 700; font-size: 19px; letter-spacing: 0.5px;
  }
  .contact-title { font-size: 13px; font-weight: 400; margin: 2px 0 12px; }
  .contact-list { list-style: none; font-size: 13px; line-height: 1.55; }
  .contact-list li { display: flex; align-items: center; gap: 7px; }
  .contact-list svg { width: 11px; height: 11px; fill: var(--brand-blue); flex: none; }
  .contact-address { font-size: 13px; line-height: 1.45; margin-top: 6px; }
  .back-brand {
    color: var(--emboss); font-weight: 700; font-size: 54px;
    letter-spacing: 8px; text-align: center; line-height: 1.1;
  }
</style>
</head>
<body>
<main class="canvas">
  <section class="card card-front">
    <svg class="wave-band" viewBox="0 0 540 309" aria-hidden="true">
      <path d="M0 150 C 30 230, 120 262, 260 272 C 380 280, 460 286, 540 276 L540 309 L0 309 Z" fill="var(--brand-blue)"/>
      <path d="M0 168 C 40 240, 130 268, 260 280 C 380 290, 460 294, 540 286" fill="none" stroke="var(--line-dark)" stroke-width="3"/>
    </svg>

    <div class="brand-name"><span class="brand-mark"></span>TA<br>BRAMLEY</div>

    <div class="divider"></div>

    <div class="contact">
      <p class="contact-name">MARCUS HALE</p>
      <p class="contact-title">Managing Director</p>
      <ul class="contact-list">
        <li><svg viewBox="0 0 24 24"><path d="M6.6 10.8a15 15 0 0 0 6.6 6.6l2.2-2.2a1 1 0 0 1 1-.25 11.4 11.4 0 0 0 3.6.57 1 1 0 0 1 1 1V20a1 1 0 0 1-1 1A17 17 0 0 1 3 4a1 1 0 0 1 1-1h3.5a1 1 0 0 1 1 1c0 1.25.2 2.45.57 3.57a1 1 0 0 1-.25 1z"/></svg>123 456 789</li>
        <li><svg viewBox="0 0 24 24"><path d="M7 1h10a2 2 0 0 1 2 2v18a2 2 0 0 1-2 2H7a2 2 0 0 1-2-2V3a2 2 0 0 1 2-2zm0 3v14h10V4zm5 15.5a1 1 0 1 0 0 2 1 1 0 0 0 0-2z"/></svg>123 456 789</li>
        <li><svg viewBox="0 0 24 24"><path d="M2 5h20v14H2zm2 2v.5l8 5 8-5V7z"/></svg>info@tabramley.com</li>
        <li><svg viewBox="0 0 24 24"><path d="M12 2a10 10 0 1 0 0 20 10 10 0 0 0 0-20zm6.9 6h-3a15 15 0 0 0-1.3-3.6A8 8 0 0 1 18.9 8zM12 4c.8 1.2 1.5 2.5 1.9 4h-3.8c.4-1.5 1.1-2.8 1.9-4zM4.3 14a8 8 0 0 1 0-4h3.4a16 16 0 0 0 0 4zm.8 2h3a15 15 0 0 0 1.3 3.6A8 8 0 0 1 5.1 16zm3-8h-3a8 8 0 0 1 4.3-3.6A15 15 0 0 0 8.1 8zM12 20c-.8-1.2-1.5-2.5-1.9-4h3.8c-.4 1.5-1.1 2.8-1.9 4zm2.3-6H9.7a14 14 0 0 1 0-4h4.6a14 14 0 0 1 0 4zm.3 5.6a15 15 0 0 0 1.3-3.6h3a8 8 0 0 1-4.3 3.6zm1.7-5.6a16 16 0 0 0 0-4h3.4a8 8 0 0 1 0 4z"/></svg>www.tabramley.com</li>
      </ul>
      <p class="contact-address">Your address, City<br>State, Zip 1234</p>
    </div>
  </section>

  <section class="card card-back">
    <div class="back-brand">TA<br>BRAMLEY</div>
  </section>
</main>
</body>
</html>
```